8x8 Social Media Ad - Brant Summit Expo

Attention Real Estate Agents
Please join us for our
Quarterly Real Estate Training Expo
The 2nd Saturday of February, May, August and November
Our Next Training Expo is _________________________________
From 9 am to 1 pm
at
Halvorne Suites Millbrook Court
4817 Copper Willow Lane, Dunmere, MD 20588
Scheduled Speakers
9:00 am - Marcus Pellington - Orientation
9:30 am - Derrin Oakfield - Multiple Income Streams / Crest Program
10:00 am - Talia Brennick - Marketing though Social Media
10:45 am - Rex Dunmore - Generating Business through Ru-Plaza
11:30 am - Kemi Adeyoro - Real Estate Investing
12:15 pm - Gregor Tamsey - (Main Speaker) Training Topic TBA
For more information call Marcus Pellington at (240) 555-0183 or email mpellington@brantsummithomes.example

```html
<!DOCTYPE html>
<html lang="en">
<head>
<meta charset="utf-8">
<title>Brant Summit Expo – Quarterly Real Estate Training Expo</title>
<link rel="stylesheet" href="https://fonts.googleapis.com/css2?family=Montserrat:wght@500;600;700;800&family=Roboto:wght@400;500;700&display=swap">
<style>
  :root{
    --teal:#21a0a0;
    --teal-text:#1f9c9a;
    --ink:#1b1b1b;
    --white:#ffffff;
    --sky-top:#9fc3d2;
    --sky-mid:#6f97a6;
    --city-low:#4d6f74;
    --avatar:#8a8a8a;
  }
  *{margin:0;padding:0;box-sizing:border-box}
  html,body{width:1200px;height:1200px;overflow:hidden;background:var(--white)}
  .ad{position:relative;width:1200px;height:1200px;background:var(--white);font-family:"Roboto",Arial,sans-serif;color:var(--ink)}
  .hero-photo{position:absolute;left:0;top:0;width:1200px;height:598px;
    background:linear-gradient(180deg,var(--sky-top) 0%,var(--sky-mid) 45%,var(--city-low) 100%)}
  .hero-shade{position:absolute;left:0;top:0;width:1200px;height:598px;background:rgba(20,60,70,.18)}
  .brand{position:absolute;top:64px;left:0;width:1200px;text-align:center;color:var(--white);font-family:"Montserrat",sans-serif}
  .brand-name{font-size:40px;font-weight:800;letter-spacing:2px;line-height:1}
  .brand-sub{margin-top:8px;font-size:13px;font-weight:800;letter-spacing:.5px;text-transform:uppercase}
  .headline{position:absolute;top:186px;left:0;width:1200px;text-align:center;color:var(--white);
    font-family:"Montserrat",sans-serif;font-weight:800;font-size:90px;line-height:94px;letter-spacing:-.5px}
  .invite{position:absolute;top:400px;left:0;width:1200px;text-align:center;color:var(--white);
    font-family:"Montserrat",sans-serif;font-weight:600;font-size:28px}
  .date-panel{position:absolute;left:100px;top:484px;width:1002px;height:175px;background:var(--teal);
    display:flex;flex-direction:column;justify-content:center;align-items:center;
    color:var(--white);font-family:"Montserrat",sans-serif;font-weight:600;font-size:30px;line-height:48px;text-align:center}
  .speakers-title{position:absolute;top:705px;left:0;width:1200px;text-align:center;
    font-family:"Montserrat",sans-serif;font-weight:700;font-size:56px;color:var(--ink)}
  .speaker{position:absolute;display:flex;align-items:flex-start}
  .speaker-photo{width:68px;height:68px;border-radius:50%;background:var(--avatar);flex:none;margin-top:0;margin-right:24px}
  .speaker-info{padding-top:2px}
  .speaker-time{font-size:15px;color:var(--ink);line-height:20px}
  .speaker-name{font-family:"Montserrat",sans-serif;font-weight:700;font-size:19px;line-height:28px;color:var(--ink)}
  .speaker-topic{font-size:15px;line-height:19px;color:var(--teal-text)}
  .contact{position:absolute;top:1108px;display:flex;align-items:center;font-size:15px;line-height:20px;color:var(--ink)}
  .contact svg{flex:none;margin-right:14px}
  .footer-band{position:absolute;left:100px;top:1175px;width:1002px;height:25px;background:var(--teal)}
</style>
</head>
<body>
<div class="ad">
  <div class="hero-photo" role="img" aria-label="Photo of a city skyline with tall residential towers under a blue sky"></div>
  <div class="hero-shade"></div>

  <div class="brand">
    <div class="brand-name">BRANT SUMMIT</div>
    <div class="brand-sub">Brant Summit Realty Group</div>
  </div>

  <h1 class="headline">Attention Real<br>Estate Agents</h1>
  <p class="invite">Please join us for our Quarterly Real Estate Training Expo</p>

  <div class="date-panel">
    <div>The 2nd Saturday of February, May, August &amp; November</div>
    <div>From 9 am to 1 pm</div>
  </div>

  <h2 class="speakers-title">Scheduled Speakers</h2>

  <div class="speaker" style="left:142px;top:812px">
    <div class="speaker-photo" role="img" aria-label="Portrait photo of Marcus Pellington"></div>
    <div class="speaker-info"><div class="speaker-time">9:00 am</div><div class="speaker-name">Marcus Pellington</div><div class="speaker-topic">Orientation</div></div>
  </div>
  <div class="speaker" style="left:478px;top:812px">
    <div class="speaker-photo" role="img" aria-label="Portrait photo of Derrin Oakfield"></div>
    <div class="speaker-info"><div class="speaker-time">9:30 am</div><div class="speaker-name">Derrin Oakfield</div><div class="speaker-topic">Multiple Income Streams /<br>Crest Program</div></div>
  </div>
  <div class="speaker" style="left:805px;top:812px">
    <div class="speaker-photo" role="img" aria-label="Portrait photo of Talia Brennick"></div>
    <div class="speaker-info"><div class="speaker-time">10:00 am</div><div class="speaker-name">Talia Brennick</div><div class="speaker-topic">Marketing though<br>Social Media</div></div>
  </div>
  <div class="speaker" style="left:142px;top:959px">
    <div class="speaker-photo" role="img" aria-label="Portrait photo of Rex Dunmore"></div>
    <div class="speaker-info"><div class="speaker-time">10:45 am</div><div class="speaker-name">Rex Dunmore</div><div class="speaker-topic">Generating Business<br>through Ru-Plaza</div></div>
  </div>
  <div class="speaker" style="left:478px;top:959px">
    <div class="speaker-photo" role="img" aria-label="Portrait photo of Kemi Adeyoro"></div>
    <div class="speaker-info"><div class="speaker-time">11:30 am</div><div class="speaker-name">Kemi Adeyoro</div><div class="speaker-topic">Real Estate Investing</div></div>
  </div>
  <div class="speaker" style="left:805px;top:959px">
    <div class="speaker-photo" role="img" aria-label="Portrait photo of Gregor Tamsey"></div>
    <div class="speaker-info"><div class="speaker-time">12:15 am</div><div class="speaker-name">Gregor Tamsey</div><div class="speaker-topic">(Main Speaker)<br>Training Topic TBA</div></div>
  </div>

  <div class="contact" style="left:100px">
    <svg width="26" height="36" viewBox="0 0 26 36" aria-hidden="true"><path d="M13 0C5.8 0 0 5.8 0 13c0 9.5 13 23 13 23s13-13.5 13-23C26 5.8 20.2 0 13 0z" fill="var(--teal)"/><circle cx="13" cy="13" r="5" fill="#fff"/></svg>
    <div>Halvorne Suites Millbrook Court 4817<br>Copper Willow Lane, Dunmere, MD 20588</div>
  </div>
  <div class="contact" style="left:568px">
    <svg width="38" height="38" viewBox="0 0 38 38" aria-hidden="true"><path d="M9 4l6 8-3 4c2 4 6 8 10 10l4-3 8 6-4 6C18 35 3 20 3 8z" fill="none" stroke="var(--teal)" stroke-width="3" stroke-linejoin="round"/><path d="M22 10a7 7 0 0 1 6 6M22 4a13 13 0 0 1 12 12" fill="none" stroke="var(--teal)" stroke-width="3" stroke-linecap="round"/></svg>
    <div>(240) 555-0183</div>
  </div>
  <div class="contact" style="left:848px;font-size:13px">
    <svg width="36" height="26" viewBox="0 0 36 26" aria-hidden="true"><rect x="1.5" y="1.5" width="33" height="23" fill="none" stroke="var(--teal)" stroke-width="3"/><path d="M2 2l16 13L34 2M2 24l12-11M34 24L22 13" fill="none" stroke="var(--teal)" stroke-width="3"/></svg>
    <div>mpellington@brantsummithomes.example</div>
  </div>

  <div class="footer-band"></div>
</div>
</body>
</html>
```